MS word document templates for consultancy

I need the following templates for my business using my logo as branding.

- General report template
- Letter head template
- Tender proposal template

The templates should be sleek and with minimal colors, but with a small amount of green and grey where appropriate (as per attached logo and email signature). Font should be consistent with the text in the email signature.

```html
<!DOCTYPE html>
<html lang="en">
<head>
<meta charset="utf-8">
<title>Northbound Advisory – Document Templates</title>
<link rel="stylesheet" href="https://fonts.googleapis.com/css2?family=Outfit:wght@300;400;500;700&display=swap">
<style>
  :root {
    --backdrop: #a8a8a8;
    --paper: #ffffff;
    --ink: #1c1c1c;
    --muted: #555555;
    --rule: #8f8f8f;
    --brand-green: #2e8b44;
  }
  * { margin: 0; padding: 0; box-sizing: border-box; }
  html, body { width: 1200px; height: 2647px; overflow: hidden; }
  body {
    background: var(--backdrop);
    font-family: "Outfit", sans-serif;
    color: var(--ink);
    position: relative;
  }
  .page { position: absolute; background: var(--paper); overflow: hidden; }
  .page > * { position: absolute; }

  .brand-header { left: 0; right: 0; display: flex; align-items: center; }
  .brand-header .header-rule { flex: 1; height: 2px; background: var(--rule); margin-top: 6px; }
  .brand-name { font-weight: 400; color: var(--ink); white-space: nowrap; letter-spacing: 0.2px; padding: 0 10px; line-height: 1.2; }
  .brand-bar { height: 5px; background: var(--brand-green); left: 0; right: 0; }

  .icon { display: inline-block; vertical-align: middle; fill: var(--muted); }
  .contact { color: var(--muted); font-weight: 300; white-space: nowrap; }

  /* Letterhead */
  .letterhead { left: 354px; top: 163px; width: 492px; height: 695px; }
  .letterhead .brand-header { top: 24px; }
  .letterhead .brand-name { font-size: 24px; }
  .letterhead .subject { left: 0; right: 0; top: 130px; text-align: center; font-size: 14px; color: #7a7a7a; font-weight: 500; letter-spacing: 0.5px; }
  .letterhead .sender-name { left: 50px; top: 199px; font-size: 14px; font-weight: 700; color: var(--brand-green); }
  .letterhead .sender-role { left: 50px; top: 217px; font-size: 12px; color: var(--muted); }
  .letter-body { left: 50px; top: 249px; width: 386px; font-size: 7.6px; line-height: 10.6px; color: #333; text-align: justify; }
  .letter-body p + p { margin-top: 22px; }
  .signature { left: 342px; top: 508px; width: 100px; height: 32px; background: linear-gradient(90deg, #f2f2f2, #e6e6e6); border-radius: 3px; }
  .sign-date { left: 342px; top: 545px; width: 100px; text-align: center; font-size: 11px; color: #333; }
  .letterhead .footer-dot { left: 243px; top: 642px; width: 6px; height: 6px; border-radius: 50%; background: var(--muted); }
  .letterhead .footer-web { left: 0; right: 0; top: 648px; text-align: center; font-size: 10px; }
  .letterhead .footer-left { left: 42px; top: 666px; font-size: 10px; }
  .letterhead .footer-right { right: 42px; top: 666px; font-size: 10px; }

  /* Covers */
  .cover .brand-header { top: 20px; }
  .cover .brand-name { padding: 0 14px; }
  .cover-year { left: 0; right: 0; text-align: center; font-weight: 700; color: var(--brand-green); font-size: 40px; }
  .cover-title { left: 0; right: 0; text-align: center; font-weight: 700; color: var(--brand-green); font-size: 45px; letter-spacing: 0.5px; }
  .cover .contact-line { font-size: 13px; }

  .report-cover { left: 302px; top: 906px; width: 596px; height: 771px; }
  .report-cover .brand-name { font-size: 36px; }
  .proposal-cover { left: 309px; top: 1729px; width: 582px; height: 754px; }
  .proposal-cover .brand-name { font-size: 35px; }
</style>
</head>
<body>

<!-- Letterhead -->
<section class="page letterhead">
  <header class="brand-header">
    <span class="header-rule"></span>
    <span class="brand-name">Northbound Advisory</span>
    <span class="header-rule"></span>
  </header>
  <div class="contact" style="right:56px;top:70px;font-size:10px">0400 555 019
    <svg class="icon" width="8" height="8" viewBox="0 0 10 10"><path d="M2 1l2 2-1 1.5c.6 1.2 1.3 1.9 2.5 2.5L7 6l2 2-1.3 1.5C4.5 9 1 5.5.5 2.3z"/></svg>
  </div>
  <div class="subject">SUBJECT</div>
  <div class="sender-name">DANIEL REEVE</div>
  <div class="sender-role">Managing Director</div>
  <div class="letter-body">
    <p>This letter sets out the scope of our advisory work for the coming year. Our team has reviewed the current structure, spoken with key staff and mapped the main risks. We found clear room to simplify reporting lines, reduce duplicated effort and give managers faster access to the figures they rely on each week. The steps below describe how we plan to move forward together.</p>
    <p>Our first phase will run over six weeks, with short check-ins at the end of each fortnight to confirm progress.</p>
    <p>During the second phase we will work closely with department leads to test new processes, gather feedback from the people who use them daily, and refine each change before it is rolled out across the wider business in stages.</p>
    <p>We look forward to your comments and will follow up next week to agree on a start date that suits you.</p>
  </div>
  <div class="signature" role="img" aria-label="Handwritten signature of Daniel Reeve"></div>
  <div class="sign-date">23/01/2025</div>
  <div class="footer-dot"></div>
  <div class="contact footer-web">www.northboundadvisory.com</div>
  <div class="contact footer-left">
    <svg class="icon" width="7" height="7" viewBox="0 0 10 10"><circle cx="5" cy="3" r="2.3"/><path d="M1 10c0-3 2-4.5 4-4.5S9 7 9 10z"/></svg>
    Dummy City, Dummy Country</div>
  <div class="contact footer-right">info@northboundadvisory.com
    <svg class="icon" width="7" height="6" viewBox="0 0 10 8"><rect width="10" height="8" rx="1"/></svg></div>
  <div class="brand-bar" style="top:685px"></div>
</section>

<!-- General report cover -->
<section class="page cover report-cover">
  <header class="brand-header">
    <span class="header-rule"></span>
    <span class="brand-name">Northbound Advisory</span>
    <span class="header-rule"></span>
  </header>
  <div class="cover-year" style="top:82px">2025</div>
  <div class="cover-title" style="top:356px">GENERAL REPORT</div>
  <div class="contact contact-line" style="left:46px;top:711px">
    <svg class="icon" width="8" height="8" viewBox="0 0 10 10"><path d="M2 1l2 2-1 1.5c.6 1.2 1.3 1.9 2.5 2.5L7 6l2 2-1.3 1.5C4.5 9 1 5.5.5 2.3z"/></svg>
    0400 555 019</div>
  <div class="contact contact-line" style="left:46px;top:727px">
    <svg class="icon" width="8" height="8" viewBox="0 0 10 10"><circle cx="5" cy="5" r="4"/></svg>
    www.northboundadvisory.com</div>
  <div class="contact contact-line" style="right:34px;top:711px">info@northboundadvisory.com
    &nbsp;<svg class="icon" width="8" height="6" viewBox="0 0 10 8"><rect width="10" height="8" rx="1"/></svg></div>
  <div class="contact contact-line" style="right:34px;top:727px">Dummy City, Dummy Country
    &nbsp;<svg class="icon" width="8" height="8" viewBox="0 0 10 10"><circle cx="5" cy="3" r="2.3"/><path d="M1 10c0-3 2-4.5 4-4.5S9 7 9 10z"/></svg></div>
  <div class="brand-bar" style="top:753px"></div>
</section>

<!-- Tender proposal cover -->
<section class="page cover proposal-cover">
  <header class="brand-header">
    <span class="header-rule"></span>
    <span class="brand-name">Northbound Advisory</span>
    <span class="header-rule"></span>
  </header>
  <div class="cover-year" style="top:80px">2025</div>
  <div class="cover-title" style="top:350px">TENDER PROPOSAL</div>
  <div class="contact contact-line" style="left:38px;top:694px;font-size:12px">
    <svg class="icon" width="8" height="8" viewBox="0 0 10 10"><path d="M2 1l2 2-1 1.5c.6 1.2 1.3 1.9 2.5 2.5L7 6l2 2-1.3 1.5C4.5 9 1 5.5.5 2.3z"/></svg>
    0400 555 019</div>
  <div class="contact contact-line" style="left:38px;top:711px;font-size:12px">
    <svg class="icon" width="8" height="8" viewBox="0 0 10 10"><circle cx="5" cy="5" r="4"/></svg>
    www.northboundadvisory.com</div>
  <div class="contact contact-line" style="right:40px;top:694px;font-size:12px">info@northboundadvisory.com
    &nbsp;<svg class="icon" width="8" height="6" viewBox="0 0 10 8"><rect width="10" height="8" rx="1"/></svg></div>
  <div class="contact contact-line" style="right:40px;top:711px;font-size:12px">Dummy City, Dummy Country
    &nbsp;<svg class="icon" width="8" height="8" viewBox="0 0 10 10"><circle cx="5" cy="3" r="2.3"/><path d="M1 10c0-3 2-4.5 4-4.5S9 7 9 10z"/></svg></div>
  <div class="brand-bar" style="top:736px"></div>
</section>

</body>
</html>
```